Business Card Design

Looking for business card designs for a new business. there will be two cards of the same design (both lots of information below in contact info). We would like the logo diagonally across the card with the information split above and below the logo similar to sketch. happy to look at similar alternatives
Please use same colours as in logo design

Industry/Entity Type

Business

Contact Information for Business Card

Dwight Halloran
mob - 0491 738 204
ph - 02 6148 3920
fax - 02 6148 3975
email - dwight@kestrelbeams.com.au
14 Larkmoor Road, Corrigan Vale NSW 2396

Colin Marchetti
mob - 0438 912 557
ph - 02 6148 3920
fax - 02 6148 3975
email - colin@kestrelbeams.com.au

```html
<!DOCTYPE html>
<html lang="en">
<head>
<meta charset="utf-8">
<title>Kestrel Beams – Business Card</title>
<link rel="stylesheet" href="https://fonts.googleapis.com/css2?family=Source+Sans+3:wght@400;600;700&display=swap">
<style>
  :root {
    --teal: #1a8b8d;
    --ink: #111111;
    --text: #2b2b2b;
    --card: #ffffff;
    --edge: #3a3a3a;
    --backdrop: #e9e7e3;
    --band-text: #ffffff;
  }
  * { box-sizing: border-box; margin: 0; padding: 0; }
  html, body {
    width: 1145px; height: 1200px; overflow: hidden;
    background: var(--backdrop);
    font-family: "Source Sans 3", "Myriad Pro", Arial, sans-serif;
  }
  .canvas { position: relative; width: 1145px; height: 1200px; }

  .card {
    position: absolute;
    width: 940px; height: 539px;
    background: var(--card);
    border: 1.5px solid var(--edge);
    overflow: hidden;
  }
  .card--front { left: 15px; top: 36px; }
  .card--back  { left: 169px; top: 609px; width: 944px; height: 538px; }

  .brand {
    position: absolute;
    display: flex; align-items: center; gap: 18px;
    color: var(--ink);
    font-weight: 700;
    line-height: 1;
    letter-spacing: -0.5px;
  }
  .brand__mark { background: var(--teal); flex: none; }
  .card--front .brand { left: 41px; top: 66px; font-size: 78px; }
  .card--front .brand__mark { width: 56px; height: 56px; }
  .card--back .brand { left: 0; right: 0; top: 205px; justify-content: center; font-size: 92px; }
  .card--back .brand__mark { width: 66px; height: 66px; }

  .contact {
    position: absolute; right: 27px; top: 267px;
    list-style: none;
    text-align: right;
    color: var(--text);
    font-size: 22px;
    line-height: 36px;
  }
  .contact li { display: flex; justify-content: flex-end; align-items: center; gap: 6px; }
  .contact svg { width: 17px; height: 17px; fill: var(--teal); flex: none; }
  .contact .contact__address { margin-top: 14px; }

  .name-band {
    position: absolute; left: 465px; right: 0; bottom: 0; height: 57px;
    background: var(--teal);
    color: var(--band-text);
    font-size: 29px; font-weight: 700;
    display: flex; align-items: center; justify-content: flex-end;
    padding-right: 31px;
  }

  .website {
    position: absolute; left: 0; right: 0; top: 426px;
    text-align: center;
    color: var(--text);
    font-size: 30px;
    letter-spacing: 2px;
  }
  .website strong { font-weight: 700; }
</style>
</head>
<body>
<main class="canvas">

  <section class="card card--front" aria-label="Business card front">
    <div class="brand"><span class="brand__mark"></span>Kestrel Beams</div>

    <ul class="contact">
      <li>
        <svg viewBox="0 0 24 24" aria-hidden="true"><path d="M6.6 10.8a15.1 15.1 0 0 0 6.6 6.6l2.2-2.2c.3-.3.7-.4 1-.2 1.1.4 2.3.6 3.6.6.6 0 1 .4 1 1V20c0 .6-.4 1-1 1A17 17 0 0 1 3 4c0-.6.4-1 1-1h3.5c.6 0 1 .4 1 1 0 1.3.2 2.5.6 3.6.1.3 0 .7-.2 1z"/></svg>
        <span>02 6148 3920</span>
      </li>
      <li>
        <svg viewBox="0 0 24 24" aria-hidden="true"><path d="M8 1h8a2 2 0 0 1 2 2v18a2 2 0 0 1-2 2H8a2 2 0 0 1-2-2V3a2 2 0 0 1 2-2zm0 3v12h8V4zm4 14a1.3 1.3 0 1 0 0 2.6 1.3 1.3 0 0 0 0-2.6z"/></svg>
        <span>0438 912 557</span>
      </li>
      <li>
        <svg viewBox="0 0 24 24" aria-hidden="true"><path d="M7 3h10v5H7zM4 9h16a2 2 0 0 1 2 2v7h-3v3H5v-3H2v-7a2 2 0 0 1 2-2zm3 7v3h10v-3z"/></svg>
        <span>02 6148 3975</span>
      </li>
      <li>
        <svg viewBox="0 0 24 24" aria-hidden="true"><path d="M2 10l10-7 10 7v10a1 1 0 0 1-1 1H3a1 1 0 0 1-1-1zm3 1.5l7 4.5 7-4.5-7-4.8z"/></svg>
        <span>colin@kestrelbeams.com.au</span>
      </li>
      <li class="contact__address"><span>14 Larkmoor Road, Corrigan Vale NSW 2396</span></li>
    </ul>

    <div class="name-band">Colin Marchetti</div>
  </section>

  <section class="card card--back" aria-label="Business card back">
    <div class="brand"><span class="brand__mark"></span>Kestrel Beams</div>
    <p class="website">www.<strong>kestrelbeams</strong>.com.au</p>
  </section>

</main>
</body>
</html>
```